Crestline Staffing PEO - Web Build for Professional Employment Organization

We need a website built for our new PEO (professional employment organization). This company will offer third party Human Resource services to companies who are looking to outsource:<br/>Recruiting<br/>Administrative Onboarding<br/>New hire training, ongoing training and development<br/>Payroll/compensation processing/services<br/>Employee Relations<br/>Unemployment Claim Facilitation<br/>Benefits Plans and Administration<br/><br/>I have attached the logo below. Please use that as a reference and color match as best as possible. <br/><br/>Here are some of the competitor's websites:<br/>https://www.velmorahr.com/ <br/>https://www.trundelpay.com/<br/>https://www.trundelpay.com/<br/>https://www.qzn.com/<br/>https://www.bremwickhr.com/<br/>https://orvalepeo.com/contact-orvale/<br/><br/>

Target Market(s)

Startups and mid-sized businesses

Number of Pages Required

5+ page

Font styles to use
Sans Serif

Colors
0592cd

Requirements
Must have
• Features Pages
• SEO driven keyword rich content
• Strong focus on our ability to provide unemployment claim facilitation services as well as mandatory training/certification fulfillment
Nice to have
• I'd like to see one mockup with a Live Chat version if possible. In theory, the Live Chat messages would go directly to our front desk person.

```html
<!DOCTYPE html>
<html lang="en">
<head>
<meta charset="utf-8">
<title>Crestline Staffing PEO – Professional Employment Organization</title>
<link rel="stylesheet" href="https://fonts.googleapis.com/css2?family=Barlow:wght@400;500;600&family=Roboto:wght@400;500&family=PT+Serif:wght@400&display=swap">
<style>
:root{
  --teal:#1e8ea6;
  --teal-soft:rgba(30,142,166,.85);
  --ink:#2f3a4a;
  --text:#5d6470;
  --muted:#7b828c;
  --line:#d9dde2;
  --grey-bg:#f2f2f2;
  --footer:#3a4457;
  --white:#fff;
}
*{box-sizing:border-box;margin:0;padding:0}
html,body{width:1200px;height:3883px;overflow:hidden}
body{position:relative;background:var(--white);font-family:"Barlow",sans-serif;color:var(--ink)}
.abs{position:absolute}

/* header */
.site-header{position:absolute;left:0;top:0;width:1200px;height:113px;border-top:5px solid var(--teal);background:var(--white)}
.brand{position:absolute;left:111px;top:36px;font-family:"Barlow",sans-serif;font-weight:600;font-size:28px;color:var(--ink);display:flex;align-items:center;gap:10px;letter-spacing:.5px}
.brand-dot{width:14px;height:14px;border-radius:50%;background:var(--teal)}
.nav a{position:absolute;top:54px;font-size:13.5px;font-weight:500;color:var(--ink);text-decoration:none;letter-spacing:.3px}
.nav a.active{color:var(--teal)}

/* hero */
.hero{position:absolute;left:0;top:113px;width:1200px;height:788px;clip-path:polygon(0 0,100% 0,100% 671px,0 100%);
  background:linear-gradient(110deg,#3d4450 0%,#8c8f97 30%,#b6b3b2 55%,#7c7c80 80%,#4a4c52 100%)}
.hero-card{position:absolute;left:671px;top:433px;width:417px;height:221px;background:var(--teal-soft);color:var(--white);text-align:center;padding-top:34px}
.hero-card h1{font-weight:400;font-size:29px;line-height:36px}
.hero-card p{font-family:"Roboto",sans-serif;font-size:11.5px;line-height:21px;margin:14px 22px 0}

/* services */
.section-title{position:absolute;left:0;width:1200px;text-align:center;font-weight:500;font-size:28px;color:var(--ink)}
.section-sub{position:absolute;left:0;width:1200px;text-align:center;font-size:15px;color:var(--text)}
.service{position:absolute;width:300px}
.service svg{display:block}
.service h3{font-weight:500;font-size:17.5px;line-height:30px;color:var(--ink);margin-top:12px}
.service p{font-family:"Roboto",sans-serif;font-size:12.5px;line-height:26px;color:var(--muted);margin-top:10px}

/* welcome */
.welcome{position:absolute;left:0;top:1676px;width:1200px;height:616px;background:var(--grey-bg)}
.welcome-photo{position:absolute;left:111px;top:70px;width:548px;height:431px;background:linear-gradient(120deg,#8a4a33,#c89a7a 45%,#e9e0d6 70%,#7a5a48)}
.welcome-card{position:absolute;left:535px;top:168px;width:552px;height:390px;background:var(--white);border:1px solid var(--line);text-align:center;padding-top:44px}
.welcome-card h2{font-weight:500;font-size:28px;color:var(--ink)}
.welcome-card h3{font-weight:500;font-size:21px;color:var(--teal);margin-top:6px}
.welcome-card p{font-family:"Roboto",sans-serif;font-size:12px;line-height:23px;color:var(--text);text-align:justify;text-align-last:center;margin:22px 48px 0}
.btn-fill{display:inline-block;margin-top:24px;width:215px;height:56px;line-height:56px;border-radius:28px;background:var(--teal);color:var(--white);font-size:18px;font-weight:500}

/* events */
.split-title{position:absolute;left:0;width:1200px;text-align:center;font-weight:500;font-size:40px;color:var(--ink)}
.split-title span{color:var(--teal)}
.underline{position:absolute;left:570px;width:60px;height:3px;background:var(--teal)}
.event{position:absolute;top:2438px;width:313px;height:499px;background:var(--white);border:1px solid var(--line);text-align:center}
.event-photo{height:228px}
.event time{display:block;margin-top:30px;font-size:15px;font-weight:500;color:var(--teal)}
.event h3{font-weight:500;font-size:19px;color:var(--ink);margin-top:10px}
.event p{font-family:"Roboto",sans-serif;font-size:12px;line-height:26px;color:var(--text);margin:14px 26px 0}
.btn-line{display:inline-block;margin-top:20px;width:134px;height:40px;line-height:38px;border:1.5px solid var(--teal);border-radius:20px;color:var(--teal);font-size:12px;font-weight:600}

/* get started */
.get-started{position:absolute;left:0;top:3011px;width:1200px;height:471px;background:linear-gradient(160deg,#f6f8fa,#edf1f4 60%,#f4f6f8)}
.field{position:absolute;height:45px;border:1px solid #cfd4d9;background:var(--white);font-family:"Roboto",sans-serif;font-size:13px;color:var(--text);padding:14px 15px}
.captcha{position:absolute;left:599px;top:3362px;width:163px;height:45px;border:1px solid #cfd4d9;background:linear-gradient(90deg,#fbeaea,#fff)}
.submit{position:absolute;left:771px;top:3362px;width:155px;height:45px;background:var(--teal);color:var(--white);font-size:20px;font-weight:500;text-align:center;line-height:45px}

/* footer */
.site-footer{position:absolute;left:0;top:3502px;width:1200px;height:381px;background:var(--footer);color:var(--white)}
.footer-brand{position:absolute;left:120px;top:140px;font-weight:600;font-size:26px;color:var(--white);display:flex;align-items:center;gap:8px}
.footer-brand i{width:12px;height:12px;border-radius:50%;background:var(--white)}
.f-col{position:absolute;top:40px;font-family:"PT Serif",serif}
.f-col h4{font-weight:400;font-size:28px;margin-bottom:18px}
.f-col li{list-style:none;position:relative;padding-left:36px}
.f-col li::before{content:"»";position:absolute;left:6px}
.links li{font-size:14px;line-height:29px}
.svc li{font-size:11px;line-height:29.5px}
.news p{font-size:12px;line-height:26px;margin-top:-4px}
.news .email{width:183px;height:45px;background:var(--white);color:#444;font-family:"Roboto",sans-serif;font-size:11px;padding:15px 18px;margin-top:20px}
.news .go{width:100px;height:37px;background:var(--teal);text-align:center;line-height:37px;font-size:17px;margin-top:10px}
.copyright{position:absolute;left:370px;top:343px;font-family:"Roboto",sans-serif;font-size:12px}
.live-chat{position:absolute;left:889px;top:328px;width:199px;height:53px;background:var(--teal);display:flex;align-items:center;justify-content:center;gap:10px;font-weight:500;font-size:17px}
</style>
</head>
<body>

<header class="site-header">
  <div class="brand"><span class="brand-dot"></span>Crestline Staffing PEO</div>
  <nav class="nav">
    <a class="active" style="left:466px">HOME</a>
    <a style="left:550px">ABOUT US</a>
    <a style="left:663px">SERVICES</a>
    <a style="left:773px">WHO WE SERVE</a>
    <a style="left:921px">NEWS</a>
    <a style="left:1007px">CONTACT US</a>
  </nav>
</header>

<section class="hero" role="img" aria-label="HR consultant interviewing a candidate across a desk in a brick-walled office"></section>
<div class="hero-card">
  <h1>Professional<br>Employment Organization</h1>
  <p>ontrary to popular belief, Lorem Ipsum is not simply random text. It has roots in a piece of classical Latin literature from 45 BC, making it over</p>
</div>

<h2 class="section-title" style="top:928px">HUMAN RESOURCE SERVICES</h2>
<svg class="abs" style="left:537px;top:972px" width="126" height="30" viewBox="0 0 126 30">
  <line x1="0" y1="15" x2="40" y2="15" stroke="#1e8ea6" stroke-width="2"/>
  <line x1="86" y1="15" x2="126" y2="15" stroke="#1e8ea6" stroke-width="2"/>
  <circle cx="63" cy="15" r="9" fill="none" stroke="#1e8ea6" stroke-width="2"/>
  <circle cx="63" cy="15" r="3" fill="#2f3a4a"/>
</svg>
<p class="section-sub" style="top:1010px">Sed ut perspiciatis unde omnis iste natus error sit voluptatem accusantium doloremque v</p>

<!-- services row 1 -->
<div class="service" style="left:111px;top:1108px">
  <svg width="82" height="82" viewBox="0 0 82 82" fill="none" stroke="#2f3a4a" stroke-width="3"><circle cx="41" cy="41" r="34"/><circle cx="41" cy="41" r="22" stroke="#1e8ea6"/><line x1="41" y1="0" x2="41" y2="16"/><line x1="41" y1="66" x2="41" y2="82"/><line x1="0" y1="41" x2="16" y2="41"/><line x1="66" y1="41" x2="82" y2="41"/><circle cx="41" cy="36" r="6"/></svg>
  <h3>Recruiting</h3>
  <p>Sed ut perspiciatis unde omnis iste natus error sit voluptatem accusantium doloremque laudan tium, totam rem aperiam, eaque</p>
</div>
<div class="service" style="left:457px;top:1108px">
  <svg width="82" height="82" viewBox="0 0 82 82" fill="none" stroke="#1e8ea6" stroke-width="3"><circle cx="20" cy="18" r="7"/><circle cx="41" cy="18" r="7"/><circle cx="62" cy="18" r="7"/><path d="M8 50v-14h64v14" stroke="#2f3a4a"/><path d="M6 70h60l10-6-10-6H6z" stroke="#2f3a4a"/></svg>
  <h3>Administrative Onboarding</h3>
  <p>Sed ut perspiciatis unde omnis iste natus error sit voluptatem accusantium doloremque laudan tium, totam rem aperiam, eaque</p>
</div>
<div class="service" style="left:802px;top:1108px">
  <svg width="82" height="82" viewBox="0 0 82 82" fill="none" stroke="#2f3a4a" stroke-width="3"><rect x="6" y="2" width="56" height="40"/><circle cx="16" cy="62" r="6" stroke="#1e8ea6"/><circle cx="34" cy="62" r="6" stroke="#1e8ea6"/><circle cx="52" cy="62" r="6" stroke="#1e8ea6"/><path d="M8 80v-8h52v8"/></svg>
  <h3>New hire training, ongoing training<br>&amp; development</h3>
  <p>Sed ut perspiciatis unde omnis iste natus error tium, totam rem aperiam, eaque</p>
</div>

<!-- services row 2 -->
<div class="service" style="left:111px;top:1396px">
  <svg width="82" height="82" viewBox="0 0 82 82" fill="none" stroke="#2f3a4a" stroke-width="3"><circle cx="38" cy="18" r="12" stroke="#1e8ea6"/><rect x="4" y="34" width="70" height="40"/><line x1="22" y1="48" x2="56" y2="48"/><line x1="22" y1="58" x2="56" y2="58"/></svg>
  <h3>Payroll/compensation processing/<br>services</h3>
  <p>Sed ut perspiciatis unde omnis iste natus error sit voluptatem accusantium doloremque laudan tium, totam rem aperiam, eaque</p>
</div>
<div class="service" style="left:457px;top:1396px">
  <svg width="82" height="82" viewBox="0 0 82 82" fill="none" stroke="#2f3a4a" stroke-width="3"><circle cx="12" cy="14" r="6"/><path d="M6 28h12l-2 44H8z"/><path d="M36 6v68M36 12h12M36 40h12M36 70h12" stroke="#1e8ea6"/><circle cx="60" cy="12" r="7" stroke="#1e8ea6"/><circle cx="60" cy="40" r="7" stroke="#1e8ea6"/><circle cx="60" cy="70" r="7" stroke="#1e8ea6"/></svg>
  <h3>Employee Relations</h3>
  <p>Sed ut perspiciatis unde omnis iste natus error sit voluptatem accusantium doloremque laudan tium, totam rem aperiam, eaque</p>
</div>
<div class="service" style="left:802px;top:1396px">
  <svg width="82" height="82" viewBox="0 0 82 82" fill="none" stroke="#2f3a4a" stroke-width="3"><rect x="10" y="14" width="62" height="52" rx="4"/><rect x="34" y="20" width="16" height="12" stroke="#1e8ea6"/><line x1="22" y1="44" x2="62" y2="44" stroke="#1e8ea6"/><line x1="22" y1="54" x2="62" y2="54"/></svg>
  <h3>Unemployment Claim Facilitation</h3>
  <p>Sed ut perspiciatis unde omnis iste natus error sit voluptatem accusantium doloremque laudan tium, totam rem aperiam, eaque</p>
</div>

<!-- welcome -->
<section class="welcome">
  <div class="welcome-photo" role="img" aria-label="Smiling woman reading a document at a laptop in a bright office"></div>
  <div class="welcome-card">
    <h2>WELCOME TO</h2>
    <h3>PROFESSIONAL EMPLOYMENT ORGANIZATION</h3>
    <p>Lorem ipsum dolor sit amet, consectetur adipiscing elit, sed do eiusmod tempor incididunt ut labore et dolore magna aliqua. Ut enim ad minim veniam, quis nostrud exercitation ullamco laboris nisi ut aliquip ex ea commodo consequat. Duis aute irure dolor in reprehenderit in voluptate velit esse cillum dolore eu fugiat nulla pariatur.Excepteur sint occaecat cupidatat non proident, sunt in culpa qui fficia deserunt mollit anim</p>
    <span class="btn-fill">VIEW MORE</span>
  </div>
</section>

<!-- events -->
<h2 class="split-title" style="top:2330px">Upcoming <span>Events</span></h2>
<div class="underline" style="top:2402px"></div>

<article class="event" style="left:111px">
  <div class="event-photo" role="img" aria-label="Smiling man in glasses reviewing papers at a meeting table" style="background:linear-gradient(120deg,#5a4a40,#8f7b6c 50%,#c9bdb2)"></div>
  <time>25 January 2020</time><h3>Lorem ipsum dolor</h3>
  <p>Sed ut perspiciatis unde omnis iste natus error sit voluptatem accusantium dolorem que laudantium, totam rem</p>
  <span class="btn-line">VIEW DETAILS</span>
</article>
<article class="event" style="left:443px">
  <div class="event-photo" role="img" aria-label="Group of colleagues in a training session around a table" style="background:linear-gradient(120deg,#3e3a38,#7a726c 50%,#bab2aa)"></div>
  <time>25 January 2020</time><h3>Lorem ipsum dolor</h3>
  <p>Sed ut perspiciatis unde omnis iste natus error sit voluptatem accusantium dolorem que laudantium, totam rem</p>
  <span class="btn-line">VIEW DETAILS</span>
</article>
<article class="event" style="left:776px">
  <div class="event-photo" role="img" aria-label="Overhead view of business people meeting at a white table" style="background:linear-gradient(120deg,#55504c,#d9d6d2 45%,#f2f1ef 60%,#6a6560)"></div>
  <time>25 January 2020</time><h3>Lorem ipsum dolor</h3>
  <p>Sed ut perspiciatis unde omnis iste natus error sit voluptatem accusantium dolorem que laudantium, totam rem</p>
  <span class="btn-line">VIEW DETAILS</span>
</article>

<!-- get started -->
<section class="get-started" role="img" aria-label="Faint background of marketing and SEO keyword words"></section>
<h2 class="split-title" style="top:3042px">Get <span>Started</span></h2>
<div class="underline" style="left:570px;top:3108px"></div>
<p class="section-sub" style="top:3133px;font-size:13.5px;font-family:'Roboto',sans-serif;color:#444">Sed ut perspiciatis unde omnis iste natus error sit voluptatem accusantium doloremque</p>
<div class="field" style="left:273px;top:3193px;width:318px">First Name*</div>
<div class="field" style="left:608px;top:3193px;width:318px">Last Name*</div>
<div class="field" style="left:273px;top:3249px;width:318px">Phone*</div>
<div class="field" style="left:608px;top:3249px;width:318px">Email*</div>
<div class="field" style="left:273px;top:3305px;width:653px">Company*</div>
<div class="field" style="left:273px;top:3362px;width:316px">Enter the Captcha</div>
<div class="captcha" role="img" aria-label="Captcha challenge image"></div>
<div class="submit">Submit</div>

<!-- footer -->
<footer class="site-footer">
  <div class="footer-brand"><i></i>Crestline Staffing PEO</div>
  <div class="f-col links" style="left:370px">
    <h4>Quick Links</h4>
    <ul><li>Home</li><li>About us</li><li>Services</li><li>Who We Serve</li><li>News</li><li>Contact us</li></ul>
  </div>
  <div class="f-col svc" style="left:593px">
    <h4>Services</h4>
    <ul><li>Recruiting</li><li>Administrative Onboarding</li><li>New hire training, ongoing training</li><li>Payroll/compensation processing/services</li><li>Employee Relations</li><li>Unemployment Claim Facilitation</li><li>Benefits Plans and Administration</li></ul>
  </div>
  <div class="f-col news" style="left:905px">
    <h4>Newsletter</h4>
    <p>Sed ut perspiciatis unde error sit<br>&nbsp;voluptatem accusantium</p>
    <div class="email">Enter Email Id :</div>
    <div class="go">Submit</div>
  </div>
  <p class="copyright">© Copyright 2020 Professional Employment Organization.All Rights Reserved</p>
  <div class="live-chat">
    <svg width="22" height="18" viewBox="0 0 22 18" fill="#fff"><path d="M2 1h12a2 2 0 0 1 2 2v6a2 2 0 0 1-2 2H7l-4 3v-3H2a2 2 0 0 1-2-2V3a2 2 0 0 1 2-2z"/><path d="M18 6h2a2 2 0 0 1 2 2v5a2 2 0 0 1-2 2h-1v3l-4-3h-4a2 2 0 0 1-2-2h6a3 3 0 0 0 3-3z"/></svg>
    LIVE CHAT
  </div>
</footer>

</body>
</html>
```